Business card for denture clinic Veltrimora

We need a new business card with our new logo. We are a denture clinic in New Zealand with our target market being 45+ years old. We would need a space on the back to write our patients next appointment on. We would space for only one appointment rather than a list. We will attach a photo showing an example of this. But of course, we would like to see your twist on this. We want it to be bold and easy to read and a good mixture of professional but modern. We have attached our logo to be used on the card.

Target Market(s)

People aged 45+ needing dentures

Industry/Entity Type

Dental

Contact Information for Business Card

We want our logo on the front and the space to write an appointment on the back. I've attached an example our our old business card showing this. We need to have the technicians details on the front.

Font styles to use
Sans Serif

Colors
0255a3
919191
fbfbfb

Requirements
Must have
• The following details:
• Liam Dorsett BDT, PGDipCDentTech Calverin
• Dental Prosthetist
• Phone numbers: 0800 47 3125
• 09 572 1394
• Email: liam@veltrimora.co.nz
• www.veltrimora.co.nz
• Address: 14 Marlow Crest Road
• Halbrook West
• Auckland 0793
Nice to have
• We would like our business cards to have more than just two colours as we want them to be more vibrant. We have uploaded an example of a business card we liked that showed this.

```html
<!DOCTYPE html>
<html lang="en">
<head>
<meta charset="utf-8">
<title>Veltrimora Business Card</title>
<link href="https://fonts.googleapis.com/css2?family=Maven+Pro:wght@400;500;700&family=Open+Sans:ital,wght@1,400&display=swap" rel="stylesheet">
<style>
  :root{
    --blue:#0267b4;
    --brand-blue:#0255a3;
    --grey-text:#5f5f5f;
    --card-grey:#7d7575;
    --rule:#8a8a8a;
    --page:#ece8e2;
    --paper:#ffffff;
    --field:#f4f4f4;
    --field-text:#8c8c8c;
  }
  *{box-sizing:border-box;margin:0;padding:0}
  html,body{width:1200px;height:987px;overflow:hidden}
  body{background:var(--page);font-family:"Maven Pro",sans-serif;position:relative}
  .card{position:absolute;left:293px;width:615px;height:352px;border-radius:18px;overflow:hidden;box-shadow:0 3px 8px rgba(0,0,0,.25)}
  .card-front{top:129px;background:var(--paper)}
  .card-back{top:505px;background:var(--card-grey)}

  .brand{position:absolute;text-align:center}
  .brand-mark{display:block;width:57px;height:56px;margin:0 auto 10px}
  .brand-name{display:block;font-weight:500;font-size:27px;letter-spacing:1px;line-height:1}
  .card-front .brand{right:23px;top:44px;width:270px}
  .card-front .brand-mark{background:var(--brand-blue)}
  .card-front .brand-name{color:var(--brand-blue)}
  .card-back .brand{left:0;right:0;top:52px}
  .card-back .brand-mark{background:#fff}
  .card-back .brand-name{color:#fff}

  .holder{position:absolute;left:29px;top:185px}
  .holder-name{font-weight:700;font-size:22px;color:var(--blue);line-height:1}
  .holder-creds{font-size:16px;margin-left:4px}
  .holder-role{font-size:17px;color:var(--grey-text);margin-top:6px}
  .divider{position:absolute;left:29px;width:563px;top:238px;border-top:1px solid var(--rule)}

  .contact{position:absolute;top:247px;font-size:16.5px;color:var(--grey-text);line-height:22px}
  .contact-phones{left:29px}
  .contact-phones b{color:var(--blue);font-weight:700}
  .contact-address{right:23px;text-align:right}

  .footer-bands{position:absolute;left:0;bottom:0;width:615px;height:36px}
  .website{position:absolute;right:24px;bottom:10px;color:#fff;font-family:"Open Sans",sans-serif;font-style:italic;font-size:15px;letter-spacing:.5px}

  .appointment-label{position:absolute;left:47px;top:232px;color:#fff;font-size:22px}
  .field{position:absolute;top:273px;width:241px;height:42px;border-radius:21px;background:var(--field);padding-left:17px;line-height:42px;font-family:"Open Sans",sans-serif;font-style:italic;font-size:17px;color:var(--field-text)}
  .field-date{left:29px}
  .field-time{left:345px}
</style>
</head>
<body>
  <section class="card card-front" aria-label="Business card front">
    <div class="brand">
      <span class="brand-mark"></span>
      <span class="brand-name">VELTRIMORA</span>
    </div>

    <div class="holder">
      <p class="holder-name">LIAM DORSETT<span class="holder-creds">BDT, PGDipCDentTech Calverin</span></p>
      <p class="holder-role">Dental Prosthetist</p>
    </div>
    <div class="divider"></div>

    <p class="contact contact-phones">
      <b>P</b> : 0800 47 3125<br>
      <b>C</b> : 09 572 1394<br>
      liam@veltrimora.co.nz
    </p>
    <p class="contact contact-address">
      14 Marlow Crest Road<br>
      Halbrook West<br>
      Auckland 0793
    </p>

    <svg class="footer-bands" viewBox="0 0 615 36" aria-hidden="true">
      <polygon points="0,20 349,20 343,36 0,36" fill="var(--blue)"/>
      <polygon points="364,0 615,0 615,36 349,36" fill="var(--card-grey)"/>
    </svg>
    <p class="website">www.veltrimora.co.nz</p>
  </section>

  <section class="card card-back" aria-label="Business card back">
    <div class="brand">
      <span class="brand-mark"></span>
      <span class="brand-name">VELTRIMORA</span>
    </div>
    <p class="appointment-label">next appointment</p>
    <div class="field field-date">date:</div>
    <div class="field field-time">time:</div>
  </section>
</body>
</html>
```